Website for a Psychologist in Private Practice

I need a cool web design for my website: www.drkalvoric.com. I would like it to look professional. Keep all the current content and add: Space for video; radio spots (see Silver Cedar Tunes Logo below for those); Quick Inquiry; Friendora link; 5 star rating on Rivo; a map; reviews from former patients. I am open to suggestions.

Target Market(s)

Those seeking individual and marital counseling.

Industry/Entity Type

Mental Health

Number of Pages Required

1 page

Font styles to use
Sans Serif
Other font styles liked:
• I'm open but no hard to read script

Requirements
Must have
• All the content on my home page with link for video and radio spots. List services and degrees and expertices (pics not necessary).
Nice to have
• A video of me and radio conversations (logo of Silver Cedar Tunes radio attached).
Should not have
• Cartoons, comedy, etc.... I don't need pictures of services (marital, depression, etc...) Just list those.

```html
<!DOCTYPE html>
<html lang="en">
<head>
<meta charset="utf-8">
<title>Dr. Marla V. Kalvoric – Clinical Psychologist</title>
<link href="https://fonts.googleapis.com/css2?family=Josefin+Sans:wght@300;400;600;700&family=Lora:wght@400&family=Roboto:wght@300;400;500;700&display=swap" rel="stylesheet">
<style>
:root{
  --gold:#c9b35a;
  --gold-dark:#b49c43;
  --blue:#2f7fc7;
  --navy:#235c8b;
  --ink:#3a3a3a;
  --muted:#6b6b6b;
  --paper:#f0efeb;
  --white:#ffffff;
  --sand-1:#e9dfd0;
  --sand-2:#d9c9b2;
  --star:#f2a21b;
}
*{box-sizing:border-box;margin:0;padding:0}
html,body{width:1200px;height:2639px;overflow:hidden}
body{position:relative;background:var(--paper);font-family:'Roboto',sans-serif;color:var(--ink)}
.abs{position:absolute}

/* header */
.site-header{left:0;top:0;width:1200px;height:100px;background:var(--white)}
.brand{left:74px;top:30px;font-family:'Josefin Sans',sans-serif;font-size:36px;color:var(--gold);font-weight:400}
.brand b{font-weight:600}
.contact-chip{display:flex;align-items:center;gap:12px;top:28px}
.chip-icon{width:44px;height:44px;border-radius:50%;background:#eef1f4;display:flex;align-items:center;justify-content:center}
.chip-text{font-size:13px;line-height:18px;color:#555;text-transform:uppercase}
.chip-text .phone{color:var(--blue);font-size:14px}

.main-nav{left:74px;top:100px;width:1052px;height:46px;background:var(--gold);display:flex;align-items:center;padding:0 8px}
.main-nav a{color:var(--white);text-decoration:none;font-family:'Roboto',sans-serif;font-weight:500;font-size:15px;padding:0 18px;border-right:1px solid rgba(255,255,255,.35);line-height:18px}
.main-nav a.active{position:relative}
.main-nav a.active::before{content:"";position:absolute;left:50%;top:-14px;margin-left:-9px;border:9px solid transparent;border-top-color:var(--blue)}
.nav-social{margin-left:auto;display:flex;gap:14px;align-items:center;color:var(--white);font-size:13px}
.nav-social span{display:flex;align-items:center;gap:5px}
.nav-social i{width:14px;height:14px;border:1.5px solid var(--white);border-radius:50%}

/* hero */
.hero{left:0;top:146px;width:1200px;height:540px;background:linear-gradient(180deg,#8fa8bd 0%,#c4b4a3 30%,#6f93ad 52%,#3b6a8c 100%)}
.hero-copy{left:0;top:200px;width:1200px;text-align:center;color:var(--white);font-family:'Lora',serif;text-shadow:0 2px 6px rgba(0,0,0,.35)}
.hero-copy .kicker{font-size:32px;line-height:40px}
.hero-copy h1{font-weight:400;font-size:50px;line-height:60px}
.hero-arrow{top:390px;width:36px;height:36px;border-radius:50%;background:rgba(255,255,255,.55);display:flex;align-items:center;justify-content:center}

/* beach band */
.beach{left:0;top:686px;width:1200px;height:634px;background:linear-gradient(180deg,#b7c9cf 0%,var(--sand-1) 40%,var(--sand-2) 100%)}
.tiles{left:60px;top:686px;width:1080px;height:246px;background:var(--white)}
.tile{top:700px;width:345px;height:224px;overflow:hidden}
.tile-caption{position:absolute;left:0;right:0;bottom:10px;color:var(--white);font-family:'Josefin Sans',sans-serif;font-weight:600;font-size:22px;text-transform:uppercase}
.tile-doctor{left:74px;background:linear-gradient(135deg,#6d8f4a,#d8c49a 55%,#7a9a58)}
.tile-doctor .tile-caption{left:14px}
.tile-video{left:428px;background:linear-gradient(135deg,#9aa7ad,#d7d0c6 50%,#7d8f97)}
.tile-video .tile-caption{text-align:center}
.play{position:absolute;left:137px;top:70px;width:72px;height:72px}
.tile-radio{left:781px;background:#5fc3c0;text-align:center}
.radio-title{position:absolute;top:18px;left:0;right:0;color:var(--white);font-family:'Josefin Sans',sans-serif;font-weight:600;font-size:23px}
.radio-art{position:absolute;left:122px;top:56px;width:102px;height:88px;border-radius:8px;background:#8a5b3a}
.radio-band{position:absolute;left:14px;right:14px;top:156px;height:30px;background:#e23e6e;color:#222;font-family:'Josefin Sans',sans-serif;font-weight:600;font-size:24px;line-height:32px}
.radio-sub{position:absolute;left:0;right:0;top:190px;color:var(--white);font-family:'Josefin Sans',sans-serif;font-weight:600;font-size:18px}

.welcome{left:90px;top:986px;width:1020px;text-align:center}
.welcome .pre{font-family:'Josefin Sans',sans-serif;font-size:26px;color:#333}
.welcome h2{font-family:'Josefin Sans',sans-serif;font-weight:400;font-size:36px;color:#222;margin-top:-4px}
.welcome h2 b{font-weight:700}
.welcome p{margin-top:18px;font-size:13.5px;line-height:24px;color:#555}
.btn-more{left:540px;top:1198px;width:122px;height:36px;border-radius:18px;background:var(--blue);color:var(--white);font-size:13px;font-weight:500;text-align:center;line-height:36px}

/* reviews */
.reviews-band{left:0;top:1320px;width:1200px;height:158px;background:var(--gold)}
.reviews-tab{left:428px;top:1299px;width:346px;height:47px;background:var(--gold);border-radius:24px 24px 0 0;color:var(--white);text-align:center;font-family:'Josefin Sans',sans-serif;font-weight:600;font-size:22px;line-height:52px}
.review{top:1417px;width:331px;height:237px;background:var(--white);box-shadow:0 2px 6px rgba(0,0,0,.08)}
.review .avatar{position:absolute;left:130px;top:-45px;width:70px;height:70px;border-radius:50%;border:3px solid var(--white);background:linear-gradient(135deg,#c79b7c,#5b4a3f)}
.review .quote-open{position:absolute;left:16px;top:-10px;font-family:'Lora',serif;font-size:72px;color:#ddd}
.review .quote-close{position:absolute;right:16px;top:140px;font-family:'Lora',serif;font-size:72px;color:#ccc;line-height:1}
.review p{position:absolute;left:30px;right:30px;top:28px;text-align:center;font-size:14px;line-height:28px;color:#555}
.review .name{position:absolute;left:30px;top:180px;font-family:'Josefin Sans',sans-serif;font-weight:600;font-size:18px;color:#222}
.review .role{position:absolute;left:30px;top:202px;font-size:12px;color:#777}
.review .stars{position:absolute;right:18px;top:198px;display:flex;gap:2px}
.review .footer-strip{position:absolute;left:0;right:0;top:168px;height:1px;background:#eee}
.divider{left:74px;top:1680px;width:1052px;height:1px;background:#c9c9c9}
.slider-dot{top:1670px;width:22px;height:22px;border-radius:50%;border:1.5px solid var(--gold);background:var(--paper);display:flex;align-items:center;justify-content:center}

/* expertise & donation */
.card{background:var(--white);box-shadow:0 1px 4px rgba(0,0,0,.08)}
.expertise{left:74px;top:1746px;width:692px;height:211px;text-align:center;padding-top:50px}
.expertise h3{font-family:'Josefin Sans',sans-serif;font-weight:400;font-size:24px;color:var(--blue)}
.expertise .list{font-family:'Josefin Sans',sans-serif;font-size:16px;color:#555;margin-top:6px;line-height:22px}
.expertise .list i{display:inline-block;width:5px;height:5px;border-radius:50%;background:#aaa;margin:0 8px;vertical-align:middle}
.expertise .sub{font-family:'Josefin Sans',sans-serif;font-size:20px;color:#555;text-transform:uppercase;line-height:26px}
.donate{left:74px;top:1989px;width:692px;height:211px;text-align:center;padding-top:40px}
.donate h4{font-family:'Josefin Sans',sans-serif;font-weight:400;font-size:22px;color:#333}
.partners{display:flex;justify-content:center;gap:70px;margin-top:28px}
.partner{display:flex;align-items:center;gap:10px;font-family:'Josefin Sans',sans-serif;font-weight:600;font-size:30px;color:var(--navy)}
.partner .mark{width:30px;height:30px;border-radius:50%;background:#d8353b}
.partner.second{color:#6a7d2a}
.partner.second .mark{background:#9bb03b;border-radius:4px}

.inquiry{left:795px;top:1746px;width:328px;height:454px}
.inquiry-head{position:absolute;left:8px;right:8px;top:8px;height:128px;background:var(--gold);clip-path:polygon(0 0,100% 0,100% 82%,50% 100%,0 82%);text-align:center;color:var(--white);padding-top:10px}
.inquiry-head .top{font-family:'Roboto',sans-serif;font-weight:500;font-size:16px}
.inquiry-head .pill{margin:6px auto 0;width:292px;height:36px;border-radius:18px;background:var(--blue);font-family:'Josefin Sans',sans-serif;font-size:28px;line-height:40px}
.inquiry-head .note{font-size:12.5px;line-height:17px;margin-top:6px}
.field{position:absolute;left:16px;width:296px;height:40px;background:#ebebeb;border-radius:3px;font-size:13px;color:#666;padding:12px}
.btn-submit{position:absolute;left:16px;top:394px;width:296px;height:40px;background:#7fa9d6;border-radius:3px;color:var(--white);font-weight:500;font-size:15px;text-align:center;line-height:40px;border-bottom:3px solid #5e8fc4}

/* footer */
.site-footer{left:0;top:2244px;width:1200px;height:343px}
.footer-col{top:2340px;width:246px;color:var(--white);font-size:13px;line-height:24px}
.footer-col h5{font-size:13px;font-weight:700;text-transform:uppercase;line-height:18px;padding-bottom:8px;border-bottom:1px solid rgba(255,255,255,.25);margin-bottom:10px}
.footer-col .row{display:flex;gap:12px;align-items:flex-start;margin-bottom:14px}
.footer-col .phone{font-size:17px}
.map{margin-top:4px;width:242px;height:160px;background:linear-gradient(135deg,#e8e6df,#d9d6cc 60%,#f0c37d)}
.footer-col a{display:block;color:var(--white);text-decoration:none}
.bottom-bar{left:0;top:2587px;width:1200px;height:52px;background:var(--gold);color:var(--white);font-size:13px}
.bottom-bar .copy{position:absolute;left:74px;top:18px}
.bottom-social{position:absolute;right:74px;top:11px;display:flex;gap:22px;align-items:center}
.bottom-social span{display:flex;align-items:center;gap:8px}
.bottom-social i{width:30px;height:30px;border-radius:50%;border:1.5px solid var(--white)}
</style>
</head>
<body>

<header class="site-header abs">
  <div class="brand abs">Dr. <b>Marla V. Kalvoric</b></div>
  <div class="contact-chip abs" style="left:652px">
    <div class="chip-icon"><svg width="20" height="20" viewBox="0 0 20 20"><path d="M2 10 L10 3 L18 10 H15 V17 H11 V12 H9 V17 H5 V10Z" fill="#2f7fc7"/></svg></div>
    <div class="chip-text">417 Tern Avenue #210<br>Coral Bay, CA. 92611</div>
  </div>
  <div class="contact-chip abs" style="left:912px">
    <div class="chip-icon"><svg width="20" height="20" viewBox="0 0 20 20"><path d="M5 2 L8 6 L6.5 8 C7.5 10.5 9.5 12.5 12 13.5 L14 12 L18 15 L16 18 C9 18 2 11 2 4Z" fill="#8aa6c1"/></svg></div>
    <div class="chip-text"><span class="phone">(555) 318 2046</span><br>MK@DRKALVORIC.COM</div>
  </div>
</header>

<nav class="main-nav abs">
  <a class="active" href="#">HOME</a>
  <a href="#">SESSIONS</a>
  <a href="#">RESOURCES</a>
  <a href="#">BIO</a>
  <a href="#">CONTACT</a>
  <div class="nav-social">
    <span><i></i>Friendora</span>
    <span><i></i>Chirpline</span>
    <span><i></i>Rivo</span>
  </div>
</nav>

<section class="hero abs" role="img" aria-label="Photo of a woman in a red dress holding a flowing red scarf on a pier above the sea at sunset"></section>
<div class="hero-copy abs">
  <div class="kicker">Lorem Ipsum Dolor Sit Amet</div>
  <h1>Consectetur Adipiscing Elit</h1>
</div>
<div class="hero-arrow abs" style="left:30px"><svg width="16" height="16" viewBox="0 0 16 16"><path d="M10 3 L5 8 L10 13" stroke="#fff" stroke-width="2" fill="none"/></svg></div>
<div class="hero-arrow abs" style="left:1134px"><svg width="16" height="16" viewBox="0 0 16 16"><path d="M6 3 L11 8 L6 13" stroke="#fff" stroke-width="2" fill="none"/></svg></div>

<section class="beach abs" role="img" aria-label="Soft photo of sea foam washing over a sandy beach"></section>
<div class="tiles abs"></div>
<div class="tile tile-doctor abs" role="img" aria-label="Portrait photo of the psychologist">
  <div class="tile-caption">Dr. Marla K</div>
</div>
<div class="tile tile-video abs" role="img" aria-label="Video still of a counseling session with three people">
  <svg class="play" viewBox="0 0 72 72"><circle cx="36" cy="36" r="33" fill="rgba(0,0,0,.25)" stroke="#fff" stroke-width="4"/><path d="M29 22 L52 36 L29 50Z" fill="#fff"/></svg>
  <div class="tile-caption">Watch Our Video</div>
</div>
<div class="tile tile-radio abs">
  <div class="radio-title">RADIO SPOTS</div>
  <div class="radio-art" role="img" aria-label="Illustration of a vintage wooden radio"></div>
  <div class="radio-band">Silver Cedar Tunes</div>
  <div class="radio-sub">With Nora and Elsie</div>
</div>

<section class="welcome abs">
  <div class="pre">Welcome to</div>
  <h2>DR. <b>MARLA V. KALVORIC</b></h2>
  <p>I'm so glad you are here.  Choosing to see a professional for issues in your life can be difficult but also possibly life changing.  Many postpone seeking help because they believe doing so acknowledges failure on their part.  Reallly?  We seek the help of experts all the time (contractors, mechanics, chefs, etc...) and what is more important than your life? Consulting with a neutral party to act in your best interest can be time well spent.  So if you are willing to take the time to invest in counseling, make sure that it is with someone that is worth your time.</p>
</section>
<div class="btn-more abs">READ MORE</div>

<div class="reviews-band abs"></div>
<div class="reviews-tab abs">REVIEWS FROM PATIENTS</div>

<article class="review abs" style="left:74px">
  <div class="quote-open">“</div><div class="avatar" role="img" aria-label="Patient portrait"></div>
  <p>Lorem ipsum dolor sit amet, consectetur adipiscing elit, sed do eiusmod tempor incididunt ut labore et dolore magna aliqua. Ut enim ad minim veniam, quis nostrud.</p>
  <div class="footer-strip"></div><div class="quote-close">”</div>
  <div class="name">John Doe</div><div class="role">Lorem Ipsum</div>
  <div class="stars"><svg width="80" height="14" viewBox="0 0 80 14"><g fill="#f2a21b"><path id="s" d="M7 0.5 L8.8 5 L13.5 5.2 L9.8 8.2 L11 13 L7 10.3 L3 13 L4.2 8.2 L0.5 5.2 L5.2 5Z"/><use href="#s" x="16"/><use href="#s" x="32"/><use href="#s" x="48"/></g><use href="#s" x="64" fill="none" stroke="#f2a21b"/></svg></div>
</article>
<article class="review abs" style="left:435px">
  <div class="quote-open">“</div><div class="avatar" role="img" aria-label="Patient portrait"></div>
  <p>Lorem ipsum dolor sit amet, consectetur adipiscing elit, sed do eiusmod tempor incididunt ut labore et dolore magna aliqua. Ut enim ad minim veniam, quis nostrud.</p>
  <div class="footer-strip"></div><div class="quote-close">”</div>
  <div class="name">John Doe</div><div class="role">Lorem Ipsum</div>
  <div class="stars"><svg width="80" height="14" viewBox="0 0 80 14"><g fill="#f2a21b"><use href="#s"/><use href="#s" x="16"/><use href="#s" x="32"/><use href="#s" x="48"/></g><use href="#s" x="64" fill="none" stroke="#f2a21b"/></svg></div>
</article>
<article class="review abs" style="left:795px">
  <div class="quote-open">“</div><div class="avatar" role="img" aria-label="Patient portrait"></div>
  <p>Lorem ipsum dolor sit amet, consectetur adipiscing elit, sed do eiusmod tempor incididunt ut labore et dolore magna aliqua. Ut enim ad minim veniam, quis nostrud.</p>
  <div class="footer-strip"></div><div class="quote-close">”</div>
  <div class="name">John Doe</div><div class="role">Lorem Ipsum</div>
  <div class="stars"><svg width="80" height="14" viewBox="0 0 80 14"><g fill="#f2a21b"><use href="#s"/><use href="#s" x="16"/><use href="#s" x="32"/><use href="#s" x="48"/></g><use href="#s" x="64" fill="none" stroke="#f2a21b"/></svg></div>
</article>

<div class="divider abs"></div>
<div class="slider-dot abs" style="left:564px"><svg width="10" height="10" viewBox="0 0 10 10"><path d="M6.5 2 L3.5 5 L6.5 8" stroke="#c9b35a" stroke-width="1.5" fill="none"/></svg></div>
<div class="slider-dot abs" style="left:614px"><svg width="10" height="10" viewBox="0 0 10 10"><path d="M3.5 2 L6.5 5 L3.5 8" stroke="#c9b35a" stroke-width="1.5" fill="none"/></svg></div>

<section class="expertise card abs">
  <h3>EXPERTISE</h3>
  <div class="list">Dating<i></i>Marriage<i></i>Parenting &amp; Professional</div>
  <div class="sub">Relationships</div>
  <div class="list">Depression &amp; Anxiety Issues<i></i>Personality Disorders<i></i>Life Management</div>
</section>

<section class="donate card abs">
  <h4>A portion of all revenue is donated to</h4>
  <div class="partners">
    <div class="partner"><span class="mark"></span>Harborlight</div>
    <div class="partner second"><span class="mark"></span>Maple Haven</div>
  </div>
</section>

<aside class="inquiry card abs">
  <div class="inquiry-head">
    <div class="top">CONTACT US TODAY FOR YOUR</div>
    <div class="pill">QUICK INQUIRY</div>
    <div class="note">Fill out the form below and we'll be in touch<br>within 24 hours!</div>
  </div>
  <div class="field" style="top:152px">Name</div>
  <div class="field" style="top:200px">Email</div>
  <div class="field" style="top:248px">Phone</div>
  <div class="field" style="top:296px;height:84px">How Can we help you?</div>
  <div class="btn-submit">SUBMIT</div>
</aside>

<footer class="site-footer abs">
  <svg width="1200" height="343" viewBox="0 0 1200 343" style="position:absolute;left:0;top:0"><path d="M0 0 C300 0 420 28 600 28 C780 28 900 0 1200 0 V343 H0Z" fill="#235c8b"/></svg>
</footer>
<div class="footer-col abs" style="left:74px">
  <h5>Clinical Psychologist<br><span style="font-weight:400">California # PSY20581</span></h5>
  Doctoral Degree in Clinical Psychology<br>Masters Degree in Counseling<br>Psychology Doctoral Internship, Bayview<br>Medical Center Masters Internship,<br>Redwood Clinic
</div>
<div class="footer-col abs" style="left:344px">
  <h5>Contact Information</h5>
  <div class="row"><svg width="18" height="20" viewBox="0 0 18 20"><path d="M9 1 C4.5 1 2 4.2 2 7.5 C2 12 9 19 9 19 C9 19 16 12 16 7.5 C16 4.2 13.5 1 9 1Z" fill="none" stroke="#fff" stroke-width="1.6"/><circle cx="9" cy="7.5" r="2.4" fill="#fff"/></svg><span style="line-height:18px">417 Tern Avenue, Suite 210<br>Coral Bay, CA 92611</span></div>
  <div class="row"><svg width="18" height="18" viewBox="0 0 20 20"><path d="M5 2 L8 6 L6.5 8 C7.5 10.5 9.5 12.5 12 13.5 L14 12 L18 15 L16 18 C9 18 2 11 2 4Z" fill="#fff"/></svg><span class="phone">(555) 318 2046</span></div>
  <div class="row"><svg width="20" height="16" viewBox="0 0 20 16"><rect x="1" y="1" width="18" height="14" fill="#fff"/><path d="M1 1 L10 9 L19 1" stroke="#235c8b" stroke-width="1.6" fill="none"/></svg><span>mk@drkalvoric.com</span></div>
</div>
<div class="footer-col abs" style="left:614px">
  <h5>Find Us On Map</h5>
  <div class="map" role="img" aria-label="Street map showing the office location with a red pin"></div>
</div>
<div class="footer-col abs" style="left:884px">
  <h5>Quick Links</h5>
  <a href="#">Home</a><a href="#">Sessions</a><a href="#">Resources</a><a href="#">Bio</a><a href="#">Contact</a>
</div>

<div class="bottom-bar abs">
  <div class="copy">©2016 Dr. Marla V. Kalvoric. All Rights Reserved.</div>
  <div class="bottom-social">
    <span><i></i>Rivo</span>
    <span><i></i>Friendora</span>
    <span><i></i>Chirpline</span>
  </div>
</div>

</body>
</html>
```